Marke für hochwertige Trauerartikel benötigt Briefpapier
Zielgruppe
Kernwald ist eine Marke für hochwertige Trauerartikel. Zielgruppe sind Bestattungsunternehmen, die nachhaltig zufriedenen Kunden möchten.
Aufgabenstellung
Wir benötigen Briefpapier: Anschreiben, Rechnngsformular in Farbe und in schwarz weiß. Dazu Visitenkarten und ein gleicherscheinenden E-Mail Absender. Das Design sollte so klar wir möglich sein. Der Druck erfolgt auf recyceltem Papier.

```html
<!DOCTYPE html>
<html lang="de">
<head>
<meta charset="utf-8">
<title>Kernwald – Briefpapier</title>
<link href="https://fonts.googleapis.com/css2?family=Source+Sans+3:ital,wght@0,400;0,600;0,700;1,600&display=swap" rel="stylesheet">
<style>
:root{
  --bg:#dcdce0;
  --paper:#ffffff;
  --gold:#c6a22e;
  --gold-pale:#f4ecd4;
  --cream:#f3ead0;
  --ink:#222222;
  --grey:#555555;
  --rule:#444444;
}
*{box-sizing:border-box;margin:0;padding:0}
html,body{width:1200px;height:936px;overflow:hidden;background:var(--bg);font-family:"Source Sans 3",sans-serif;color:var(--ink)}
.canvas{position:relative;width:1200px;height:936px}
.sheet{position:absolute;width:310px;height:439px;background:var(--paper);overflow:hidden}
.sheet--letter{left:61px;top:224px}
.sheet--letter-alt{left:408px;top:230px}
.sheet--invoice{left:771px;top:229px}
.abs{position:absolute}
.brand{position:absolute;display:flex;align-items:center;gap:3px;font-weight:700;font-size:9px;color:var(--gold);letter-spacing:.2px;white-space:nowrap}
.brand__mark{width:7px;height:7px;border:1px solid var(--ink)}
.decor{position:absolute;border-radius:50% 0 0 50%;background:radial-gradient(circle at 100% 50%,var(--gold-pale) 0%,#faf6ea 60%,rgba(255,255,255,0) 75%)}
.fine{font-size:5px;line-height:1.35;color:var(--grey)}
.gold-tab{position:absolute;background:var(--gold)}
.contact{position:absolute;display:flex;gap:3px;align-items:flex-start;font-size:4.6px;line-height:1.3;color:var(--grey)}
.contact__icon{width:9px;height:9px;background:var(--gold);border-radius:1.5px;display:flex;align-items:center;justify-content:center}
.invoice-title{position:absolute;left:28px;top:52px;font-size:12.5px;font-weight:700;letter-spacing:.3px}
.invoice-title span{color:var(--gold);margin-left:4px}
.invoice-date{position:absolute;left:28px;top:69px;font-size:6px}
.invoice-date b{font-weight:700}
.client-head{position:absolute;left:28px;top:107px;font-size:6px;font-weight:700}
.client{position:absolute;left:28px;top:117px;font-size:5.5px;line-height:1.32;display:grid;grid-template-columns:32px auto}
.sender{position:absolute;right:39px;top:94px;text-align:right;font-size:5.5px;line-height:1.35;color:var(--grey)}
table.grid{position:absolute;border-collapse:collapse;font-size:4.4px;font-weight:700}
table.grid th{background:var(--cream);border:1px solid var(--rule);height:9px;font-weight:700}
table.grid td{border:1px solid var(--rule);height:8px}
.comment{position:absolute;left:27px;top:282px;width:128px;height:36px;border:1px solid var(--rule)}
.comment__head{background:var(--cream);font-size:5.5px;font-weight:700;padding:1px 8px;height:10px}
.totals{position:absolute;left:236px;top:280px;width:41px;border-collapse:collapse}
.totals td{border:1px solid var(--rule);height:9.5px}
.total-label{position:absolute;left:205px;top:305px;font-size:7px;font-weight:700}
.thanks{position:absolute;left:28px;top:351px;font-size:5.8px;font-style:italic;font-weight:600}
.band{position:absolute;top:409px;height:24px;background:var(--gold);color:#fff;font-size:4.6px;line-height:1.3;font-weight:600}
.band--left{left:0;width:226px;padding:3px 8px;display:flex;gap:8px}
.band--left .divider{width:1px;background:#fff;align-self:stretch;margin:2px 0}
.band--right{left:281px;width:29px}
.base-line{position:absolute;left:0;bottom:3px;width:310px;height:3px;background:var(--ink)}
</style>
</head>
<body>
<main class="canvas">

  <!-- Anschreiben, Variante A -->
  <section class="sheet sheet--letter">
    <div class="brand" style="left:31px;top:62px"><i class="brand__mark"></i>Kernwald</div>
    <div class="decor" role="img" aria-label="Große blassgoldene Blütenornament-Dekoration am rechten Rand" style="left:168px;top:73px;width:142px;height:315px"></div>
    <p class="fine abs" style="right:24px;top:390px;text-align:right">RC: 3071 - patente: 60218834 - IF: 5193027<br>CNSS: 7304862 - ICE: 00731946000052<br>Tél: +49 431 555 0188 - Email: post@kernwald-mail.de - Website: www.kernwald-mail.de</p>
    <div class="gold-tab" style="left:299px;top:388px;width:11px;height:20px"></div>
  </section>

  <!-- Anschreiben, Variante B -->
  <section class="sheet sheet--letter-alt">
    <div class="brand" style="left:41px;top:62px"><i class="brand__mark"></i>Kernwald</div>
    <div class="decor" role="img" aria-label="Große blassgoldene Blütenornament-Dekoration am rechten Rand" style="left:175px;top:81px;width:135px;height:293px"></div>
    <div class="abs" style="left:36px;top:400px;width:241px;height:1px;background:var(--rule)"></div>
    <div class="contact" style="left:40px;top:407px">
      <span class="contact__icon"><svg width="6" height="6" viewBox="0 0 24 24"><path fill="#fff" d="M6.6 10.8a15 15 0 0 0 6.6 6.6l2.2-2.2c.3-.3.7-.4 1-.2 1.1.4 2.3.6 3.6.6.6 0 1 .4 1 1V20c0 .6-.4 1-1 1A17 17 0 0 1 3 4c0-.6.4-1 1-1h3.5c.6 0 1 .4 1 1 0 1.3.2 2.5.6 3.6.1.3 0 .7-.2 1z"/></svg></span>
      <span>0431555017<br>0431555029</span>
    </div>
    <div class="contact" style="left:109px;top:407px">
      <span class="contact__icon"><svg width="6" height="6" viewBox="0 0 24 24"><circle cx="12" cy="12" r="4" fill="none" stroke="#fff" stroke-width="3"/><path d="M16 8v5a3 3 0 0 0 6 0v-1a10 10 0 1 0-4 8" fill="none" stroke="#fff" stroke-width="3"/></svg></span>
      <span>kontakt@kernwald-info.de<br>www.kernwald-info.de</span>
    </div>
    <div class="contact" style="left:186px;top:407px">
      <span class="contact__icon"><svg width="6" height="6" viewBox="0 0 24 24"><path fill="#fff" d="M12 3 2 12h3v9h5v-6h4v6h5v-9h3z"/></svg></span>
      <span>Birkenallee 7 | 24105<br>Kiel</span>
    </div>
  </section>

  <!-- Rechnungsformular -->
  <section class="sheet sheet--invoice">
    <h1 class="invoice-title">INVOICE<span>1345</span></h1>
    <p class="invoice-date"><b>Date:</b> 31 nov, 2020</p>
    <div class="abs" style="left:68px;top:96px;width:72px;height:1px;background:var(--gold)"></div>
    <div class="brand" style="left:230px;top:64px"><i class="brand__mark"></i>Kernwald</div>
    <p class="sender">Lindenweg 14<br>24103 Kiel<br>Tél: +49 431 555 0142<br>Email: info@kernwald-post.de<br>Website: www.kernwald-post.de</p>
    <h2 class="client-head">FACTURE A LINTENTION DE:</h2>
    <div class="client">
      <span>NOM:</span><span>Nom de la société</span>
      <span>ADRESSE:</span><span>Contact, Greta exemple<br>adresse Exemple adresse</span>
      <span>TEL:</span><span>0431 555 0000</span>
      <span>EMAIL:</span><span>kunde@beispielpost.de</span>
    </div>

    <table class="grid" style="left:27px;top:181px;width:250px">
      <tr><th>Description</th><th>Unité</th><th>Quantité</th><th>Montant</th><th>Prix ttc</th><th>Totale</th></tr>
      <tr><td></td><td></td><td></td><td></td><td></td><td></td></tr>
    </table>
    <table class="grid" style="left:27px;top:208px;width:250px">
      <tr><th style="width:89px">Description</th><th>Quantité</th><th>Montant</th><th>Prix ttc</th><th>Totale</th></tr>
      <tr><td></td><td></td><td></td><td></td><td></td></tr>
      <tr><td></td><td></td><td></td><td></td><td></td></tr>
      <tr><td></td><td></td><td></td><td></td><td></td></tr>
      <tr><td></td><td></td><td></td><td></td><td></td></tr>
      <tr><td></td><td></td><td></td><td></td><td></td></tr>
    </table>

    <div class="comment"><p class="comment__head">Other comment or other instruction</p></div>
    <table class="totals"><tr><td></td></tr><tr><td></td></tr><tr><td></td></tr><tr><td></td></tr></table>
    <p class="total-label">Totale</p>

    <p class="thanks">THANK YOU FOR YOUR BUSINESS!</p>

    <div class="band band--left">
      <span>RC: 2847 - patente: 6173908<br>IF: 4091735 - CNSS: 8165203<br>ICE: 002683914000041</span>
      <span class="divider"></span>
      <span style="padding-top:3px">Lindenweg 14<br>24103 Kiel</span>
    </div>
    <div class="brand" style="left:230px;top:417px;font-size:7px"><i class="brand__mark"></i>Kernwald</div>
    <div class="band band--right"></div>
    <div class="base-line"></div>
  </section>

</main>
</body>
</html>
```